Meridale Bed Company Needs Business Card

Looking for a very nice looking business card. Creative but not extravagant. We sell beds and pillows across the U.S. and need something professional but catchy. I have attached the logo.

Name : Devin Holt
Title : President
Phone : (800) 471-2960
Email: sleep@quilmora.com
Website: www.quilmora.com

Can be single-sided or double-sided
horizontal or vertical

Can use Blues/Greys

Target Market(s)

Mass Market

Industry/Entity Type

Retail

Contact Information for Business Card

Name : Devin Holt
Title : President
Phone : (800) 471-2960
Email: sleep@quilmora.com
Website: www.quilmora.com

Requirements
Must have
• Clean, Modern, Smooth
• Can use Blues/Greys
• On the other side without the information - have something simple like www.quilmora.com or our logo
Nice to have
• Surprise me
Should not have
• Nothing crazy, nothing cluttered

```html
<!DOCTYPE html>
<html lang="en">
<head>
<meta charset="utf-8">
<title>Quilmora Business Card</title>
<link rel="stylesheet" href="https://fonts.googleapis.com/css2?family=Montserrat:wght@300;400;500;700&display=swap">
<style>
  :root {
    --ink: #212226;
    --sky: #33a4d6;
    --paper: #ffffff;
    --backdrop: #e4e6ea;
  }
  * { margin: 0; padding: 0; box-sizing: border-box; }
  html, body {
    width: 1200px;
    height: 1200px;
    overflow: hidden;
    background: var(--backdrop);
    font-family: "Montserrat", sans-serif;
  }
  .canvas {
    position: relative;
    width: 1200px;
    height: 1200px;
  }
  .card {
    position: absolute;
    top: 169px;
    width: 444px;
    height: 834px;
    overflow: hidden;
  }
  .card--back {
    left: 115px;
    background: var(--sky);
  }
  .card--back .top-band {
    position: absolute;
    left: 0; top: 0;
    width: 100%;
    height: 419px;
    background: var(--ink);
  }
  .card--back .wordmark {
    position: absolute;
    left: 0; right: 0;
    top: 378px;
    text-align: center;
    color: var(--paper);
    font-weight: 300;
    font-size: 58px;
    line-height: 70px;
    letter-spacing: 1px;
  }
  .card--back .footer-url {
    position: absolute;
    left: 0; right: 0;
    bottom: 50px;
    text-align: center;
    color: var(--ink);
    font-weight: 500;
    font-size: 19px;
  }
  .card--front {
    left: 626px;
    background: var(--paper);
    color: var(--sky);
    text-align: center;
  }
  .person-name {
    position: absolute;
    left: 0; right: 0;
    top: 172px;
    font-weight: 700;
    font-size: 43px;
    line-height: 50px;
  }
  .person-title {
    position: absolute;
    left: 0; right: 0;
    top: 228px;
    font-weight: 400;
    font-size: 27px;
    letter-spacing: 1.5px;
    line-height: 32px;
  }
  .card--front .wordmark {
    position: absolute;
    left: 0; right: 0;
    top: 338px;
    font-weight: 300;
    font-size: 72px;
    line-height: 86px;
    letter-spacing: 1px;
  }
  .contact {
    position: absolute;
    left: 0; right: 0;
    top: 513px;
    list-style: none;
    font-weight: 500;
    font-size: 28px;
    line-height: 47.5px;
  }
</style>
</head>
<body>
  <main class="canvas">
    <section class="card card--back" aria-label="Card back">
      <div class="top-band"></div>
      <div class="wordmark">quilmora</div>
      <div class="footer-url">www.quilmora.com</div>
    </section>

    <section class="card card--front" aria-label="Card front">
      <h1 class="person-name">Devin Holt</h1>
      <p class="person-title">PRESIDENT</p>
      <div class="wordmark">quilmora</div>
      <ul class="contact">
        <li>sleep@quilmora.com</li>
        <li>www.quilmora.com</li>
        <li>(800) 471-2960</li>
      </ul>
    </section>
  </main>
</body>
</html>
```